Pinecrest Real Estate A5 Flyer

A5 Flyer for print distribution.

Front (include attached photo and branding):
Pinecrest are a new face in the Dunmore & Kelvinhurst real estate market. The Pinecrest team are both Dunmore ‘locals’ and are genuinely and sincerely committed to this community. They put people first and pursue exceptional outcomes for their clients. This is the founding vision of Pinecrest.

Values:
Outstanding Customer Service
Timely Communication
Integrity Always
People First
Exceptional Negotiation

If you’re thinking of selling, interested in a free market appraisal, or simply want to find out more about the Pinecrest team, please reach out to Trevor or Owen for a chat. We’d love to shout you a coffee at The Marigold Coffee + Kitchen.

Pinecrest Real Estate
E: hello@pinecrestrealestate-example.com.au
W: pinecrestrealestate-example.com.au

Back (half the page about Trevor, other half the page about Owen). Please include headshots (Owen is the younger one):

Owen Pritchard (Property Consultant):

Owen has an in-depth understanding of all things property & finance related. With a degree in property & finance, diploma in finance & mortgage broking, certificate IV in real estate practice, project management roles in residential property development, plus years of small business experience as co-founder/co-owner of The Marigold Coffee + Kitchen, his experience in managing competing demands and complex scenarios runs far and wide.

Owen also has experience in corporate negotiations which is proving to be a very beneficial skill set. Owen is deeply committed to people and pursuing exceptional outcomes for his clients. He has built a reputation as a man of his word who is genuine and sincere and willing to go above and beyond for his clients.

owen@pinecrestrealestate-example.com.au
0400 118 204

Trevor Bungey (Director / Licensee):

Trevor has worked in various roles inclusive of being a Real Estate Agent, Bank Manager, Financial Counsellor, Mortgage Broker, and previously a Commercial Pilot. He spent eight years in remote Western Australia, where he worked for an international mining company creating strategies to help support the well-being of employees. Trevor’s focus in life has always been to help people. To him, it is always about the relationship. Trevor gets enormous satisfaction from seeing individuals, families, and businesses thrive financially. He has become a skilled negotiator with extensive experience working for a number of corporations and private firms.
 
What differentiates Trevor is his compassion and commitment to people. He works hard to be an excellent communicator with the aim of achieving great results. He  has extensive sales experience with incredible ability to push the boundaries, think outside the box and meet or surpass expectations. This is why his clients keep coming back and continue to refer well into the future. 

trevor@pinecrestrealestate-example.com.au
0400 362 917

Target Market(s)

House Sellers / House Buyers

Industry/Entity Type

Real Estate

Colors
0054AA
0677BA
7BADD7
CADEEF
E8F1F8

Requirements
Must have
• Branding / logo, river photo, head shots, company details etc
Nice to have
• Design as per attached branding guide

```html
<!DOCTYPE html>
<html lang="en">
<head>
<meta charset="utf-8">
<title>Pinecrest Real Estate – A5 Flyer</title>
<link href="https://fonts.googleapis.com/css2?family=Cormorant+Garamond:wght@500&family=DM+Serif+Display&family=Poppins:wght@400;500;600&display=swap" rel="stylesheet">
<style>
  :root {
    --slate: #747e98;
    --slate-light: #8a93aa;
    --navy: #131c2b;
    --ink: #2b2f38;
    --bar-dark: #3a404c;
    --bar-mid: #737a88;
    --paper: #ffffff;
    --backdrop: #eceef1;
    --rule: #c9ccd4;
  }
  * { box-sizing: border-box; margin: 0; padding: 0; }
  html, body { width: 803px; height: 1200px; overflow: hidden; background: var(--backdrop); }
  body { font-family: "Poppins", sans-serif; color: var(--ink); position: relative; }

  .sheet { position: absolute; top: 326px; width: 386px; height: 548px; box-shadow: 0 2px 8px rgba(0,0,0,0.12); background: var(--paper); overflow: hidden; }
  .sheet--front { left: 10px; }
  .sheet--back { left: 407px; }
  .page { position: relative; width: 585px; height: 830px; transform: scale(0.66); transform-origin: 0 0; background: var(--paper); }

  /* ---------- front ---------- */
  .brand-band {
    position: absolute; left: 32px; top: 30px; width: 521px; height: 90px;
    background: var(--slate);
    display: flex; align-items: center; justify-content: center; gap: 18px;
  }
  .brand-dot { width: 54px; height: 54px; border-radius: 50%; background: var(--navy); }
  .brand-name { font-family: "Cormorant Garamond", serif; font-weight: 500; font-size: 32px; letter-spacing: 10px; color: var(--navy); }

  .photo { position: absolute; border: 1.5px solid var(--navy); }
  .photo--river { left: 32px; top: 135px; width: 271px; height: 286px;
    background: linear-gradient(180deg, #9fb2c8 0%, #5f7890 35%, #3c5468 70%, #2e3c2f 100%); }
  .photo--family { left: 313px; top: 135px; width: 240px; height: 140px;
    background: linear-gradient(180deg, #e9edf0 0%, #c7ccd2 55%, #6d8a3d 100%); }
  .photo--pool-home { left: 313px; top: 282px; width: 240px; height: 140px;
    background: linear-gradient(180deg, #c9917a 0%, #7e6a5f 45%, #5d8ea3 75%, #c9c6c0 100%); }
  .photo--villa { left: 313px; top: 428px; width: 240px; height: 140px;
    background: linear-gradient(180deg, #8fb3d6 0%, #d8dde0 50%, #c7b9a3 75%, #4e6b3a 100%); }

  .title-box {
    position: absolute; left: 32px; top: 287px; width: 252px; height: 134px;
    background: var(--navy); color: var(--paper);
    font-family: "DM Serif Display", serif; font-size: 40px; line-height: 1.05;
    padding: 22px 0 0 18px;
  }
  .intro { position: absolute; left: 32px; top: 452px; width: 272px; font-size: 10.8px; line-height: 1.25; }

  .values-frame { position: absolute; left: 32px; top: 583px; width: 521px; height: 108px; border-right: 1.2px solid var(--rule); border-bottom: 1.2px solid var(--rule); }
  .values-frame::before { content: ""; position: absolute; left: 210px; right: 0; top: 0; height: 1.2px; background: var(--rule); }
  .values-tab { position: absolute; left: 32px; top: 570px; width: 200px; height: 27px; }
  .values-tab .bar { position: absolute; left: 0; top: 0; width: 4px; height: 27px; background: var(--navy); }
  .values-tab svg { position: absolute; left: 6px; top: 0; }
  .values-tab .label { position: absolute; left: 20px; top: 3px; font-size: 17px; font-weight: 500; color: var(--paper); }
  .values-list { position: absolute; left: 32px; top: 600px; width: 521px; display: flex; justify-content: space-between; padding: 0 6px 0 0; }
  .value { display: flex; flex-direction: column; align-items: center; text-align: center; white-space: nowrap; }
  .value-icon { width: 34px; height: 34px; border-radius: 50%; background: var(--slate); border: 2px solid #dfe2e8; display: flex; align-items: center; justify-content: center; }
  .value-name { margin-top: 7px; font-size: 11.5px; line-height: 1.2; }
  .values-marker { position: absolute; left: 86px; top: 686px; width: 5px; height: 5px; border-radius: 50%; background: var(--navy); }

  .invite { position: absolute; left: 32px; top: 706px; width: 524px; font-size: 10.8px; line-height: 1.25; }

  /* ---------- shared footer ---------- */
  .footer-strip { position: absolute; left: 0; top: 752px; width: 585px; height: 9px; }
  .footer { position: absolute; left: 0; top: 762px; width: 585px; height: 68px; }
  .footer svg.footer-shape { position: absolute; left: 0; top: 0; }
  .footer-item { position: absolute; top: 0; height: 68px; display: flex; align-items: center; gap: 8px; font-size: 10.4px; color: var(--paper); white-space: nowrap; }
  .footer-item--email { left: 24px; }
  .footer-item--web { left: 348px; }
  .footer-icon { width: 18px; height: 18px; border-radius: 50%; background: #a6adbd; display: flex; align-items: center; justify-content: center; flex: none; }

  /* ---------- back ---------- */
  .profile { position: absolute; left: 32px; width: 521px; }
  .profile--owen { top: 30px; }
  .profile--trevor { top: 318px; }
  .headshot { position: absolute; left: 0; top: 0; width: 114px; height: 114px; border-radius: 50%; z-index: 2;
    background: radial-gradient(circle at 50% 45%, #d9dbde 0%, #b9bcc1 60%, #9ea3aa 100%); }
  .name-tab { position: absolute; left: 92px; top: 14px; z-index: 1; }
  .name { position: absolute; left: 125px; top: 16px; z-index: 3; font-size: 16px; font-weight: 600; color: var(--paper); letter-spacing: 0.2px; }
  .role { position: absolute; left: 125px; top: 45px; font-size: 10.5px; font-weight: 500; color: var(--navy); }
  .bio { position: absolute; left: 0; top: 66px; width: 521px; font-size: 10px; line-height: 12.8px; }
  .bio .wrap-space { float: left; width: 125px; height: 51px; }
  .bio p + p { margin-top: 6px; }

  .contact-bar { position: absolute; left: 32px; width: 521px; height: 36px; background: var(--bar-mid); display: flex; align-items: center; color: var(--paper); }
  .contact-bar--owen { top: 262px; }
  .contact-bar--trevor { top: 582px; }
  .contact-phone { width: 158px; height: 36px; background: var(--bar-dark); display: flex; align-items: center; gap: 8px; padding-left: 10px; font-size: 15px; font-weight: 500; }
  .contact-email { display: flex; align-items: center; gap: 8px; padding-left: 10px; font-size: 12.3px; font-weight: 500; white-space: nowrap; }
  .contact-icon { width: 20px; height: 20px; border-radius: 50%; background: var(--paper); display: flex; align-items: center; justify-content: center; flex: none; }

  .gallery { position: absolute; left: 32px; top: 632px; width: 521px; height: 112px; display: flex; gap: 8px; }
  .gallery .photo { position: static; flex: 1; height: 112px; }
  .photo--river-aerial { background: linear-gradient(180deg, #c5ccd3 0%, #7d8b98 40%, #3f5668 70%, #2f3b33 100%); }
  .photo--dark-home { background: linear-gradient(180deg, #b9bdc2 0%, #5a5f66 45%, #2f3338 80%, #3d4a34 100%); }
  .photo--white-home { background: linear-gradient(180deg, #2f5e93 0%, #9db7cf 40%, #e8e6e0 65%, #3a7ea0 100%); }
</style>
</head>
<body>

<section class="sheet sheet--front" aria-label="Flyer front">
  <div class="page">
    <header class="brand-band">
      <span class="brand-dot"></span>
      <span class="brand-name">PINECREST</span>
    </header>

    <div class="photo photo--river" role="img" aria-label="Aerial photo of the river foreshore with suburbs and city skyline"></div>
    <div class="title-box">Pinecrest<br>Real Estate</div>
    <div class="photo photo--family" role="img" aria-label="Photo of a young family walking together on a lawn"></div>
    <div class="photo photo--pool-home" role="img" aria-label="Photo of a modern home with a swimming pool at dusk"></div>
    <div class="photo photo--villa" role="img" aria-label="Photo of a large white villa with gardens"></div>

    <p class="intro">Pinecrest are a new face in the Dunmore &amp; Kelvinhurst real estate market. The Pinecrest team are both Dunmore ‘locals’ and are genuinely and sincerely committed to this community. They put people first and pursue exceptional outcomes for their clients. This is the founding vision of Pinecrest.</p>

    <div class="values-frame"></div>
    <div class="values-tab">
      <span class="bar"></span>
      <svg width="194" height="27" viewBox="0 0 194 27"><polygon points="0,0 176,0 194,27 0,27" fill="var(--slate)"/></svg>
      <span class="label">OUR VALUES</span>
    </div>
    <div class="values-list">
      <div class="value"><span class="value-icon"><svg width="16" height="16" viewBox="0 0 22 22" fill="#fff"><circle cx="11" cy="6" r="4"/><path d="M3 20c0-5 4-8 8-8s8 3 8 8z"/></svg></span><span class="value-name">Outstanding<br>Customer Service</span></div>
      <div class="value"><span class="value-icon"><svg width="16" height="16" viewBox="0 0 22 22" fill="none" stroke="#fff" stroke-width="2"><circle cx="11" cy="11" r="8"/><path d="M11 6v5l3 3"/></svg></span><span class="value-name">Timely<br>Communication</span></div>
      <div class="value"><span class="value-icon"><svg width="16" height="16" viewBox="0 0 22 22" fill="none" stroke="#fff" stroke-width="2.4"><path d="M4 11l5 5 9-10"/></svg></span><span class="value-name">Integrity<br>Always</span></div>
      <div class="value"><span class="value-icon"><svg width="16" height="16" viewBox="0 0 22 22" fill="#fff"><circle cx="6" cy="8" r="3"/><circle cx="16" cy="8" r="3"/><circle cx="11" cy="6" r="3"/><path d="M1 18c0-4 4-6 10-6s10 2 10 6z"/></svg></span><span class="value-name">People<br>First</span></div>
      <div class="value"><span class="value-icon"><svg width="16" height="16" viewBox="0 0 22 22" fill="#fff"><rect x="2" y="3" width="8" height="7" rx="1"/><rect x="12" y="3" width="8" height="7" rx="1"/><circle cx="6" cy="14" r="2.5"/><circle cx="16" cy="14" r="2.5"/><path d="M2 21c0-3 2-4 4-4s4 1 4 4zM12 21c0-3 2-4 4-4s4 1 4 4z"/></svg></span><span class="value-name">Exceptional<br>Negotiation</span></div>
    </div>
    <span class="values-marker"></span>

    <p class="invite">If you’re thinking of selling, interested in a free market appraisal, or simply want to find out more about the Pinecrest team, please reach out to Trevor or Owen for a chat. We’d love to shout you a coffee at The Marigold Coffee + Kitchen.</p>

    <svg class="footer-strip" viewBox="0 0 585 9" preserveAspectRatio="none"><polygon points="160,0 585,0 585,9 170,9" fill="var(--slate-light)"/></svg>
    <footer class="footer">
      <svg class="footer-shape" width="585" height="68" viewBox="0 0 585 68">
        <rect width="585" height="68" fill="var(--slate)"/>
        <polygon points="0,0 314,0 328,34 314,68 0,68" fill="var(--navy)"/>
        <polygon points="318,0 325,0 339,34 325,68 318,68 332,34" fill="var(--paper)"/>
      </svg>
      <div class="footer-item footer-item--email">
        <span class="footer-icon"><svg width="10" height="7" viewBox="0 0 14 10"><rect x="0.5" y="0.5" width="13" height="9" fill="#fff"/><path d="M0.5 0.5l6.5 5 6.5-5" fill="none" stroke="#8a93aa"/></svg></span>
        <span>hello@pinecrestrealestate-example.com.au</span>
      </div>
      <div class="footer-item footer-item--web">
        <span class="footer-icon"><svg width="12" height="12" viewBox="0 0 16 16" fill="none" stroke="#fff" stroke-width="1.3"><circle cx="8" cy="8" r="6.5"/><ellipse cx="8" cy="8" rx="3" ry="6.5"/><path d="M1.5 8h13"/></svg></span>
        <span>pinecrestrealestate-example.com.au</span>
      </div>
    </footer>
  </div>
</section>

<section class="sheet sheet--back" aria-label="Flyer back">
  <div class="page">
    <article class="profile profile--owen">
      <div class="headshot" role="img" aria-label="Headshot of Owen Pritchard"></div>
      <svg class="name-tab" width="222" height="27" viewBox="0 0 222 27"><polygon points="0,0 196,0 212,27 0,27" fill="var(--slate)"/><polygon points="199,0 206,0 222,27 215,27" fill="var(--bar-dark)"/></svg>
      <h2 class="name">OWEN PRITCHARD</h2>
      <p class="role">Property Consultant</p>
      <div class="bio">
        <span class="wrap-space"></span>
        <p>Owen has an in-depth understanding of all things property &amp; finance related. With a degree in property &amp; finance, diploma in finance &amp; mortgage broking, certificate IV in real estate practice, project management roles in residential property development, plus years of small business experience as co-founder/co-owner of The Marigold Coffee + Kitchen, his experience in managing competing demands and complex scenarios runs far and wide.</p>
        <p>Owen also has experience in corporate negotiations which is proving to be a very beneficial skill set. Owen is deeply committed to people and pursuing exceptional outcomes for his clients. He has built a reputation as a man of his word who is genuine and sincere and willing to go above and beyond for his clients.</p>
      </div>
    </article>
    <div class="contact-bar contact-bar--owen">
      <span class="contact-phone"><span class="contact-icon"><svg width="11" height="11" viewBox="0 0 16 16"><path d="M3 1l3 3-2 2c1 2 4 5 6 6l2-2 3 3-2 2C7 15 1 9 1 3z" fill="var(--bar-dark)"/></svg></span>0400 118 204</span>
      <span class="contact-email"><span class="contact-icon"><svg width="11" height="8" viewBox="0 0 14 10"><rect x="0.5" y="0.5" width="13" height="9" fill="var(--bar-mid)"/><path d="M0.5 0.5l6.5 5 6.5-5" fill="none" stroke="#fff"/></svg></span>owen@pinecrestrealestate-example.com.au</span>
    </div>

    <article class="profile profile--trevor">
      <div class="headshot" role="img" aria-label="Headshot of Trevor Bungey"></div>
      <svg class="name-tab" width="202" height="27" viewBox="0 0 202 27"><polygon points="0,0 176,0 192,27 0,27" fill="var(--slate)"/><polygon points="179,0 186,0 202,27 195,27" fill="var(--bar-dark)"/></svg>
      <h2 class="name">TREVOR BUNGEY</h2>
      <p class="role">Director / Licensee</p>
      <div class="bio">
        <span class="wrap-space"></span>
        <p>Trevor has worked in various roles inclusive of being a Real Estate Agent, Bank Manager, Financial Counsellor, Mortgage Broker, and previously a Commercial Pilot. He spent eight years in remote Western Australia, where he worked for an international mining company creating strategies to help support the well-being of employees. Trevor’s focus in life has always been to help people. To him, it is always about the relationship. Trevor gets enormous satisfaction from seeing individuals, families, and businesses thrive financially. He has become a skilled negotiator with extensive experience working for a number of corporations and private firms.</p>
        <p>What differentiates Trevor is his compassion and commitment to people. He works hard to be an excellent communicator with the aim of achieving great results. He has extensive sales experience with incredible ability to push the boundaries, think outside the box and meet or surpass expectations. This is why his clients keep coming back and continue to refer well into the future.</p>
      </div>
    </article>
    <div class="contact-bar contact-bar--trevor">
      <span class="contact-phone"><span class="contact-icon"><svg width="11" height="11" viewBox="0 0 16 16"><path d="M3 1l3 3-2 2c1 2 4 5 6 6l2-2 3 3-2 2C7 15 1 9 1 3z" fill="var(--bar-dark)"/></svg></span>0400 362 917</span>
      <span class="contact-email"><span class="contact-icon"><svg width="11" height="8" viewBox="0 0 14 10"><rect x="0.5" y="0.5" width="13" height="9" fill="var(--bar-mid)"/><path d="M0.5 0.5l6.5 5 6.5-5" fill="none" stroke="#fff"/></svg></span>trevor@pinecrestrealestate-example.com.au</span>
    </div>

    <div class="gallery">
      <div class="photo photo--river-aerial" role="img" aria-label="Aerial photo of the river and city skyline"></div>
      <div class="photo photo--dark-home" role="img" aria-label="Photo of a modern dark-clad home among trees"></div>
      <div class="photo photo--white-home" role="img" aria-label="Photo of a white modern home with a pool"></div>
    </div>

    <svg class="footer-strip" viewBox="0 0 585 9" preserveAspectRatio="none"><polygon points="160,0 585,0 585,9 170,9" fill="var(--slate-light)"/></svg>
    <footer class="footer">
      <svg class="footer-shape" width="585" height="68" viewBox="0 0 585 68">
        <rect width="585" height="68" fill="var(--slate)"/>
        <polygon points="0,0 314,0 328,34 314,68 0,68" fill="var(--navy)"/>
        <polygon points="318,0 325,0 339,34 325,68 318,68 332,34" fill="var(--paper)"/>
      </svg>
      <div class="footer-item footer-item--email">
        <span class="footer-icon"><svg width="10" height="7" viewBox="0 0 14 10"><rect x="0.5" y="0.5" width="13" height="9" fill="#fff"/><path d="M0.5 0.5l6.5 5 6.5-5" fill="none" stroke="#8a93aa"/></svg></span>
        <span>hello@pinecrestrealestate-example.com.au</span>
      </div>
      <div class="footer-item footer-item--web">
        <span class="footer-icon"><svg width="12" height="12" viewBox="0 0 16 16" fill="none" stroke="#fff" stroke-width="1.3"><circle cx="8" cy="8" r="6.5"/><ellipse cx="8" cy="8" rx="3" ry="6.5"/><path d="M1.5 8h13"/></svg></span>
        <span>pinecrestrealestate-example.com.au</span>
      </div>
    </footer>
  </div>
</section>

</body>
</html>
```